K & R Acre Works. Business card design

We need a business card designed for a new business. We have a bulldozer and tractor service. We clear land and make wildlife food plots. We provide disking, bush hogging, and site prep services.
I have attached an image of a business card that I like and would like my business cards to look similar.

Target Market(s)

anyone needing bulldozer and/or tractor services

Industry/Entity Type

Business

Contact Information for Business Card

K & R Acre Works, Operated by 7-T-Ranch
Wade Colton
601-472-3358
wcr4817@fieldmail-example.com

Font styles to use
Sans Serif

Colors

Designer to choose colors to be used in the design.

Requirements
Must have
• image of tractor and bulldozer
• Land Clearing
• Wildlife food plots
• Bush Hogging
• Disking
• Site prep
Nice to have
• i have included a image of a business card that i like. I would like mine to be similar.

```html
<!DOCTYPE html>
<html lang="en">
<head>
<meta charset="utf-8">
<title>K &amp; R Acre Works – Business Card</title>
<link href="https://fonts.googleapis.com/css2?family=Bebas+Neue&family=Roboto+Condensed:wght@400&display=swap" rel="stylesheet">
<style>
  :root {
    --page-bg: #e9e6e1;
    --band-black: #000000;
    --rule-white: #ffffff;
    --brand-red: #e8182a;
    --text-white: #ffffff;
    --photo-dark: #141712;
    --photo-green: #2b3524;
    --photo-red: #6a2a1c;
  }
  html, body {
    margin: 0;
    padding: 0;
    width: 1200px;
    height: 930px;
    overflow: hidden;
    background: var(--page-bg);
  }
  .business-card {
    position: absolute;
    left: 120px;
    top: 190px;
    width: 960px;
    height: 550px;
    border-radius: 30px;
    overflow: hidden;
    background: var(--photo-dark);
  }
  .card-header {
    position: absolute;
    left: 0; top: 0;
    width: 100%;
    height: 84px;
    background: var(--band-black);
    border-bottom: 6px solid var(--rule-white);
    display: flex;
    align-items: center;
    justify-content: center;
    z-index: 2;
  }
  .company-line {
    margin: 0;
    font-family: "Bebas Neue", sans-serif;
    font-weight: 400;
    font-size: 44px;
    color: var(--brand-red);
    line-height: 1;
    padding-top: 6px;
  }
  .equipment-photo {
    position: absolute;
    left: 0; top: 90px;
    width: 100%;
    height: 460px;
    background:
      radial-gradient(ellipse 45% 55% at 45% 55%, var(--photo-red) 0%, rgba(106,42,28,0.35) 55%, rgba(0,0,0,0) 80%),
      linear-gradient(180deg, var(--photo-green) 0%, #1f2419 55%, #2a2a20 100%);
    z-index: 0;
  }
  .photo-shade {
    position: absolute;
    left: 0; top: 90px;
    width: 100%;
    height: 460px;
    background: rgba(0,0,0,0.25);
    z-index: 1;
  }
  .identity-row {
    position: absolute;
    left: 0;
    top: 270px;
    width: 100%;
    display: flex;
    justify-content: center;
    align-items: center;
    gap: 28px;
    z-index: 2;
  }
  .owner-name {
    margin: 0;
    font-family: "Bebas Neue", sans-serif;
    font-weight: 400;
    font-size: 76px;
    line-height: 1;
    padding-top: 8px;
    color: var(--text-white);
    white-space: nowrap;
  }
  .name-divider {
    width: 2px;
    height: 62px;
    background: var(--text-white);
    flex: none;
  }
  .contact-list {
    margin: 0;
    padding: 0;
    list-style: none;
    font-family: "Roboto Condensed", sans-serif;
    font-size: 29px;
    line-height: 40px;
    color: var(--text-white);
  }
  .contact-item {
    display: flex;
    align-items: center;
    gap: 14px;
    white-space: nowrap;
  }
  .contact-icon {
    width: 22px;
    height: 22px;
    flex: none;
  }
  .service-list {
    position: absolute;
    left: 0;
    top: 474px;
    width: 100%;
    margin: 0;
    text-align: center;
    font-family: "Bebas Neue", sans-serif;
    font-size: 36px;
    line-height: 1;
    color: var(--text-white);
    z-index: 2;
  }
</style>
</head>
<body>
  <article class="business-card">
    <header class="card-header">
      <h1 class="company-line">K &amp; R Acre Works, Operated by 7-T-Ranch</h1>
    </header>

    <div class="equipment-photo" role="img" aria-label="Photo of a red tractor with front loader in a cleared field"></div>
    <div class="photo-shade"></div>

    <div class="identity-row">
      <h2 class="owner-name">Wade Colton</h2>
      <div class="name-divider"></div>
      <ul class="contact-list">
        <li class="contact-item">
          <svg class="contact-icon" viewBox="0 0 24 24" aria-hidden="true">
            <path d="M6.6 2.5 9 5.6c.4.5.3 1.2-.1 1.6L7.4 8.6c1 2.6 3.3 5.1 6 6.4l1.5-1.5c.4-.4 1.1-.5 1.6-.1l3 2.4c.5.4.6 1.1.2 1.6l-1.6 2c-.5.6-1.3.9-2.1.7C9.6 18.6 5.4 14.4 3.9 8c-.2-.8.1-1.600.7-2.1l2-1.6" fill="none" stroke="#fff" stroke-width="1.6" stroke-linejoin="round"/>
          </svg>
          <span>601-472-3358</span>
        </li>
        <li class="contact-item">
          <svg class="contact-icon" viewBox="0 0 24 24" aria-hidden="true">
            <rect x="2.5" y="5.5" width="19" height="13" rx="1.5" fill="none" stroke="#fff" stroke-width="1.8"/>
            <path d="M3 6.5 12 13l9-6.5" fill="none" stroke="#fff" stroke-width="1.8" stroke-linejoin="round"/>
          </svg>
          <span>wcr4817@fieldmail-example.com</span>
        </li>
      </ul>
    </div>

    <p class="service-list">Land Clearing – Wildlife Food Plots – Bush Hogging – Disking – Site Prep</p>
  </article>
</body>
</html>
```